Corvalle Gelato Pints

6 flavors , pints italian , southern , organic , natural feel

Pistachio , chocolate, strawberry , hazelnut , vaniglia

Stracciiatelle

Target Market(s)

Upscale

Requirements
Must have
• See graphic upload . Want that look.. showing freshbest quality in gradients of each flavor

```html
<!DOCTYPE html>
<html lang="en">
<head>
<meta charset="utf-8">
<title>Corvalle Gelato Pints – Strawberry Stracciatelle Label</title>
<link rel="stylesheet" href="https://fonts.googleapis.com/css2?family=Open+Sans:wght@400;700&display=swap">
<style>
  :root {
    --canvas-bg: #e4e4e4;
    --label-red-deep: #c4060c;
    --label-red: #e3231f;
    --label-red-light: #f2664d;
    --band-red: #cf0d14;
    --text-white: #f4f1f1;
    --text-maroon: #6e0d10;
    --text-dark: #2a0a0a;
  }
  * { margin: 0; padding: 0; box-sizing: border-box; }
  html, body {
    width: 1200px;
    height: 960px;
    overflow: hidden;
    background: var(--canvas-bg);
    font-family: "Open Sans", Arial, sans-serif;
  }
  .canvas {
    position: relative;
    width: 1200px;
    height: 960px;
    display: flex;
    align-items: center;
    justify-content: center;
  }
  .label {
    position: relative;
    width: 740px;
    height: 800px;
    overflow: hidden;
  }
  .label-texture {
    position: absolute;
    inset: 0;
    background:
      radial-gradient(ellipse at 75% 20%, rgba(255,120,90,0.35), transparent 55%),
      linear-gradient(165deg, var(--label-red-deep) 0%, var(--label-red) 45%, var(--label-red-light) 100%);
  }
  .label-content {
    position: relative;
    height: 100%;
    display: flex;
    flex-direction: column;
    align-items: center;
    padding-top: 110px;
  }
  .brand-name {
    font-weight: 700;
    font-size: 150px;
    line-height: 1;
    color: var(--text-white);
    letter-spacing: 2px;
  }
  .brand-line {
    align-self: flex-end;
    margin-right: 70px;
    margin-top: 6px;
    font-weight: 700;
    font-size: 54px;
    color: var(--text-white);
  }
  .flavor-band {
    margin-top: 70px;
    width: 560px;
    padding: 10px 0;
    background: var(--band-red);
    text-align: center;
    font-weight: 400;
    font-size: 60px;
    line-height: 1.15;
    color: var(--text-white);
    letter-spacing: 1px;
  }
  .flavor-sub {
    margin-top: 14px;
    font-size: 62px;
    color: var(--text-maroon);
  }
  .tagline {
    margin-top: 22px;
    font-size: 28px;
    line-height: 1.35;
    text-align: center;
    color: var(--text-dark);
  }
</style>
</head>
<body>
  <main class="canvas">
    <section class="label">
      <div class="label-texture" role="img" aria-label="Strawberry red mosaic texture in soft gradient"></div>
      <div class="label-content">
        <h1 class="brand-name">Corvalle</h1>
        <p class="brand-line">Gelato Pints</p>
        <p class="flavor-band">STRAWBERRY</p>
        <p class="flavor-sub">Stracciatelle</p>
        <p class="tagline">Pints Italian , Southern , Organic<br>Natural Feel</p>
      </div>
    </section>
  </main>
</body>
</html>
```